Modern design company business card design

We are a design oriented construction firm. The owner is an architect and licensed General Contractor and accomplished furniture designer. We do new home construction and large scale remodeling and office design. We would like a design for our new business cards that is clean and modern, but relatable. We like the bright green color of our logo mixed with different shades of grey. We're also open to reinterpreting the logo.

Target Market(s)

Potential design clients,
Construction clients

Industry/Entity Type

Architecture

Contact Information for Business Card

Tall Maple Design | Build Inc. (optional with logo, Inc. optional)Jeffrey MorganOwner (optional)317.555.0148 cell317.431.8056 officejmorgan@greensquareinc.comwww.greensquareinc.com

Font styles to use
Sans Serif
Other font styles liked:
• Avenir

Requirements
Nice to have
• I like designs that have some continuity between the front and back, i.e. similar layouts or graphic elements that wrap around the card. I tend to prefer horizontal over vertical, but that's not a have to. I also tend to prefer white or recycled paper.

```html
<!DOCTYPE html>
<html lang="en">
<head>
<meta charset="utf-8">
<title>Tall Maple Design | Build Inc. — Business Card</title>
<link rel="stylesheet" href="https://fonts.googleapis.com/css2?family=Jost:wght@300;400&display=swap">
<style>
  :root {
    --page: #ececec;
    --card: #ffffff;
    --green: #8cc63f;
    --grey-dark: #3d3d3d;
    --grey-mid: #6d6d6d;
    --grey-light: #9a9a9a;
    --ink: #2a2a2a;
  }
  * { margin: 0; padding: 0; box-sizing: border-box; }
  html, body {
    width: 1105px; height: 1200px; overflow: hidden;
    background: var(--page);
    font-family: "Jost", "Avenir", sans-serif;
  }
  .card {
    position: absolute; left: 196px; width: 720px; height: 410px;
    background: var(--card);
    border: 1px solid #dcdcdc;
  }
  .card--front { top: 146px; }
  .card--back { top: 602px; }

  .wordmark {
    position: absolute; left: 84px; top: 200px;
    display: inline-flex; flex-direction: column; align-items: flex-end;
  }
  .brand-name {
    font-size: 36px; font-weight: 400; letter-spacing: 2px;
    color: var(--grey-mid); line-height: 1;
  }
  .brand-tagline {
    margin-top: 8px;
    font-size: 15px; font-weight: 400; letter-spacing: 1.6px;
    color: var(--grey-light); line-height: 1;
  }
  .corner-mark {
    position: absolute; width: 120px; height: 120px;
    background: var(--grey-dark); border-radius: 50%;
  }
  .card--front .corner-mark { left: 576px; top: 262px; }
  .card--back .corner-mark { left: 28px; top: 262px; }

  .person-name {
    position: absolute; left: 368px; top: 172px;
    font-size: 30px; font-weight: 400; color: var(--green);
    letter-spacing: 0.5px; line-height: 1;
  }
  .person-role {
    position: absolute; left: 368px; top: 212px;
    font-size: 20px; font-weight: 400; color: var(--grey-mid);
    line-height: 1;
  }
  .contact-list {
    position: absolute; left: 368px; top: 270px; list-style: none;
  }
  .contact-list li {
    display: flex; align-items: center; height: 28px;
    font-size: 19px; color: var(--ink);
  }
  .contact-list svg { width: 17px; height: 17px; margin-right: 12px; fill: var(--green); flex: none; }
</style>
</head>
<body>
  <section class="card card--front" aria-label="Card front">
    <div class="wordmark">
      <div class="brand-name">TALL MAPLE</div>
      <div class="brand-tagline">DESIGN | BUILD</div>
    </div>
    <div class="corner-mark"></div>
  </section>

  <section class="card card--back" aria-label="Card back">
    <div class="corner-mark"></div>
    <h1 class="person-name">DENNIS HOLLOWAY</h1>
    <p class="person-role">OWNER</p>
    <ul class="contact-list">
      <li>
        <svg viewBox="0 0 24 24"><path d="M6.6 10.8a15.1 15.1 0 0 0 6.6 6.6l2.2-2.2a1 1 0 0 1 1-.25 11.4 11.4 0 0 0 3.6.57 1 1 0 0 1 1 1V20a1 1 0 0 1-1 1A17 17 0 0 1 3 4a1 1 0 0 1 1-1h3.5a1 1 0 0 1 1 1c0 1.25.2 2.45.57 3.57a1 1 0 0 1-.25 1z"/></svg>
        317.555.0148
      </li>
      <li>
        <svg viewBox="0 0 24 24"><path d="M7 1h10a2 2 0 0 1 2 2v18a2 2 0 0 1-2 2H7a2 2 0 0 1-2-2V3a2 2 0 0 1 2-2zm0 3v15h10V4zm5 16.2a1 1 0 1 0 0 .01z"/></svg>
        317.555.0172
      </li>
      <li>
        <svg viewBox="0 0 24 24"><circle cx="12" cy="12" r="10"/></svg>
        www.tallmapleinc.example
      </li>
      <li>
        <svg viewBox="0 0 24 24"><path d="M2 5h20v2l-10 6L2 7zm0 4l10 6 10-6v10H2z"/></svg>
        dholloway@tallmapleinc.example
      </li>
    </ul>
  </section>
</body>
</html>
```